Vorn upkeep KT Solar Venture

Solar power system install
Services and maintenance
wiring, Rewinding and Renovation
Switch Board Upgrade
Power and lighting point
t doesn’t matter how much you spend on quality parts, your solar system will let you down if your design and installation are sub-par. Have your solar system tailored and installed by our Master Electrician and Bright Grid Guild Accredited team.

Target Market(s)

sales and installed

Industry/Entity Type

Solar install and retailer

Contact Information for Business Card

Name , Email, Phone Number ,Business address,

Font styles to use
Serif

Colors
0054AA
0677BA
7BADD7
CADEEF
E8F1F8

Requirements
Must have
• clear and bright
Nice to have
• new design
Should not have
• unclear pictures

```html
<!DOCTYPE html>
<html lang="en">
<head>
<meta charset="utf-8">
<title>Vorn upkeep – KT Solar Venture business card</title>
<link href="https://fonts.googleapis.com/css2?family=Roboto:wght@400;500&family=Roboto+Condensed:wght@700&display=swap" rel="stylesheet">
<style>
  :root {
    --backdrop: #2d2d2d;
    --blue-deep: #0054AA;
    --blue-mid: #0677BA;
    --blue-light: #7BADD7;
    --blue-pale: #CADEEF;
    --blue-mist: #E8F1F8;
    --green: #2f9e3a;
    --paper: #f2f3f3;
    --ink: #1d2430;
    --white: #ffffff;
  }
  * { margin: 0; padding: 0; box-sizing: border-box; }
  html, body {
    width: 1200px; height: 1138px; overflow: hidden;
    background: var(--backdrop);
    font-family: "Roboto", Arial, sans-serif;
  }
  .card {
    position: absolute;
    border-radius: 16px;
    overflow: hidden;
  }
  /* Front */
  .card-front {
    left: 274px; top: 186px; width: 623px; height: 376px;
    background: linear-gradient(180deg, var(--blue-deep) 0%, var(--blue-mid) 100%);
  }
  .card-front .art { position: absolute; inset: 0; }
  .front-brand {
    position: absolute; right: 31px; top: 78px;
    display: flex; align-items: center; gap: 14px;
  }
  .brand-dot {
    width: 58px; height: 58px; border-radius: 50%;
    background: var(--blue-pale);
    flex: none;
  }
  .brand-name {
    font-family: "Roboto Condensed", "Arial Narrow", sans-serif;
    font-weight: 700; text-transform: uppercase;
    line-height: 1.05; letter-spacing: 0.5px;
  }
  .front-brand .brand-name { color: var(--white); font-size: 25px; }
  .service-list {
    position: absolute; right: 30px; top: 229px;
    list-style: none; text-align: right;
    color: var(--white); font-size: 16px; line-height: 22.3px;
  }
  .service-list li::after { content: "\00AB"; margin-left: 10px; }

  /* Back */
  .card-back {
    left: 276px; top: 608px; width: 618px; height: 374px;
    background: var(--paper);
  }
  .card-back .waves { position: absolute; inset: 0; }
  .back-brand {
    position: absolute; left: 50px; top: 56px; width: 240px;
    display: flex; flex-direction: column; align-items: center;
  }
  .back-brand .brand-dot { width: 104px; height: 104px; background: var(--blue-mist); border: 3px solid var(--blue-light); margin-bottom: 30px; }
  .back-brand .brand-name { color: var(--blue-deep); font-size: 31px; text-align: center; }
  .holder {
    position: absolute; right: 28px; top: 40px; text-align: right; color: var(--ink);
  }
  .holder-name { font-size: 26px; font-weight: 500; color: var(--blue-deep); line-height: 1.2; }
  .holder-role { font-size: 16px; margin-top: 4px; }
  .holder-address { font-size: 16px; line-height: 24px; margin-top: 22px; font-style: normal; }
  .contact-list {
    position: absolute; right: 26px; top: 269px;
    list-style: none; color: var(--white); font-size: 16px; line-height: 24px;
  }
  .contact-list li { display: flex; justify-content: flex-end; align-items: center; gap: 14px; }
  .contact-list svg { width: 14px; height: 14px; fill: var(--blue-pale); flex: none; }
</style>
</head>
<body>

<section class="card card-front" aria-label="Card front">
  <svg class="art" viewBox="0 0 623 376" preserveAspectRatio="none">
    <defs>
      <linearGradient id="photoTone" x1="0" y1="0" x2="1" y2="1">
        <stop offset="0" stop-color="#5f6f86"/>
        <stop offset="0.35" stop-color="#3a4660"/>
        <stop offset="1" stop-color="#23283a"/>
      </linearGradient>
      <linearGradient id="sunGlow" x1="1" y1="0" x2="0" y2="0.6">
        <stop offset="0" stop-color="#d9a36f" stop-opacity="0.75"/>
        <stop offset="1" stop-color="#d9a36f" stop-opacity="0"/>
      </linearGradient>
      <linearGradient id="edgeGreen" x1="0" y1="0" x2="0" y2="1">
        <stop offset="0.25" stop-color="#2f9e3a" stop-opacity="0"/>
        <stop offset="0.6" stop-color="#2f9e3a"/>
      </linearGradient>
    </defs>
    <g role="img" aria-label="Photograph of solar panels catching sunlight">
      <path d="M0,0 L205,0 Q347,188 205,376 L0,376 Z" fill="url(#photoTone)"/>
      <path d="M0,0 L205,0 Q347,188 205,376 L0,376 Z" fill="url(#sunGlow)"/>
    </g>
    <path d="M205,0 Q347,188 205,376" fill="none" stroke="url(#edgeGreen)" stroke-width="7"/>
  </svg>

  <div class="front-brand">
    <span class="brand-dot" aria-hidden="true"></span>
    <div class="brand-name">Vorn Upkeep<br>KT Solar Venture</div>
  </div>

  <ul class="service-list">
    <li>Solar Power System Install</li>
    <li>Services &amp; Maintenance</li>
    <li>Switch Board Upgrade</li>
    <li>Power &amp; Lighting Point</li>
    <li>Wiring, Rewinding &amp; Renovation</li>
  </ul>
</section>

<section class="card card-back" aria-label="Card back">
  <svg class="waves" viewBox="0 0 618 374" preserveAspectRatio="none" aria-hidden="true">
    <path d="M0,322 C130,372 270,360 390,290 C470,245 540,226 618,232 L618,374 L0,374 Z" fill="var(--blue-mid)"/>
    <path d="M0,322 C130,372 270,360 390,290 C470,245 540,226 618,232 L618,374 L0,374 Z" fill="var(--blue-deep)" opacity="0.35"/>
    <path d="M0,294 C140,330 300,322 410,262 C490,218 550,204 618,212" fill="none" stroke="var(--green)" stroke-width="9"/>
    <path d="M0,310 C110,345 230,345 300,320" fill="none" stroke="#7cc243" stroke-width="6" stroke-linecap="round"/>
  </svg>

  <div class="back-brand">
    <span class="brand-dot" aria-hidden="true"></span>
    <div class="brand-name">Vorn Upkeep<br>KT Solar Venture</div>
  </div>

  <div class="holder">
    <h1 class="holder-name">Dana Reyes Cole</h1>
    <p class="holder-role">Managing Director</p>
    <address class="holder-address">58 Harbor Lane, Milltown,<br>Eastvale, US 204417</address>
  </div>

  <ul class="contact-list">
    <li>555-014-2290
      <svg viewBox="0 0 24 24" aria-label="Phone"><path d="M6.6 10.8a15 15 0 0 0 6.6 6.6l2.2-2.2c.3-.3.7-.4 1-.2 1.1.4 2.3.6 3.6.6.6 0 1 .4 1 1V20c0 .6-.4 1-1 1A17 17 0 0 1 3 4c0-.6.4-1 1-1h3.5c.6 0 1 .4 1 1 0 1.3.2 2.5.6 3.6.1.3 0 .7-.2 1z"/></svg>
    </li>
    <li>dana@vornupkeep.example
      <svg viewBox="0 0 24 24" aria-label="Email"><path d="M2 5h20v14H2z M4 7v.5l8 5 8-5V7l-8 5z" fill-rule="evenodd"/></svg>
    </li>
    <li>www.vornupkeep.example
      <svg viewBox="0 0 24 24" aria-label="Website"><path d="M12 2a10 10 0 1 0 0 20 10 10 0 0 0 0-20zm0 2c.9 1.2 1.6 2.9 1.9 5h-3.8c.3-2.1 1-3.8 1.9-5zM4.3 11h3.8c0 .7.1 1.4.2 2H4.3a8 8 0 0 1 0-2zm5.8 0h3.8a12 12 0 0 1 0 2h-3.8a12 12 0 0 1 0-2zm5.8 0h3.8a8 8 0 0 1 0 2h-3.8c.1-.6.1-1.3 0-2zM12 20c-.9-1.2-1.6-2.9-1.9-5h3.8c-.3 2.1-1 3.8-1.9 5z"/></svg>
    </li>
  </ul>
</section>

</body>
</html>
```